Business Card Design Project - Sports Brand

Brisk is a e-commerce fitness wear brand for ladies who are into gym, pole and swim.

Card should not be overly cluttered and should include the following:

1. logo
2. Name of the company (Use "Brisk Loom Pte Ltd" for now)
3. Address of company (Use a mock address)
4. Representative's name and contact info etc. (use a mock name and contact info)
5. website address

Target Market(s)

Women who are into pole , gym, and swim.

Women who shop online

Industry/Entity Type

E-Commerce

Colors

Designer to choose colors to be used in the design.

Requirements
Nice to have
• feminine sublimation of colours

Need not be printed on traditional paper. We would like the design to be revolutionary and interesting to the eye :)
Should not have
• the design should not be traditional looking. Do not include illustrations of Bikinis, yoga poses etc. in the card.

```html
<!DOCTYPE html>
<html lang="en">
<head>
<meta charset="utf-8">
<title>Brisk Loom – Business Card</title>
<link href="https://fonts.googleapis.com/css2?family=Lora:wght@400;500&display=swap" rel="stylesheet">
<style>
  :root{
    --backdrop:#e9e7e4;
    --pink:#e2589b;
    --pink-soft:#ec7fb0;
    --orange:#ea5a24;
    --berry:#c42a4a;
    --rose:#e0407f;
    --ink:#6b6b6b;
    --white:#ffffff;
  }
  *{margin:0;padding:0;box-sizing:border-box}
  html,body{width:1200px;height:1000px;overflow:hidden}
  body{
    background:var(--backdrop);
    font-family:"Lora",Georgia,serif;
    position:relative;
  }
  .card{
    position:absolute;
    left:330px;
    width:540px;height:320px;
    box-shadow:0 6px 18px rgba(0,0,0,.18);
    overflow:hidden;
  }
  /* Front */
  .card--front{
    top:110px;
    background:linear-gradient(100deg,var(--pink) 0%,var(--pink-soft) 38%,#ee8a5e 58%,var(--orange) 80%,var(--orange) 100%);
  }
  .front-brand{
    position:absolute;left:48px;top:60px;
    display:flex;align-items:center;gap:22px;
  }
  .front-brand .mark{
    width:200px;height:200px;border-radius:50%;
    background:var(--white);
    display:flex;align-items:center;justify-content:center;
  }
  .front-brand .mark .brand-name{
    font-size:62px;color:var(--pink);font-weight:500;
  }
  .front-tagline{
    color:var(--white);font-size:24px;letter-spacing:.5px;
  }
  /* Back */
  .card--back{
    top:560px;
    background:var(--white);
  }
  .back-brand{
    position:absolute;left:40px;top:50px;width:200px;
    display:flex;flex-direction:column;align-items:center;
  }
  .back-brand .dot{
    width:150px;height:150px;border-radius:50%;
    background:radial-gradient(circle at 40% 40%,#f06a8c,var(--pink) 55%,#d9468a 100%);
  }
  .back-brand .brand-name{
    margin-top:14px;font-size:46px;color:var(--berry);font-weight:500;line-height:1;
  }
  .back-brand .tagline{
    margin-top:8px;font-size:15px;color:var(--ink);
  }
  .contact{
    position:absolute;left:290px;top:44px;right:24px;
  }
  .person-name{font-size:22px;color:var(--rose);letter-spacing:.5px}
  .person-role{font-size:16px;color:var(--ink);margin:2px 0 14px}
  .contact-list{list-style:none}
  .contact-list li{
    display:flex;align-items:center;gap:10px;
    font-size:15px;color:var(--ink);margin-bottom:8px;
  }
  .icon{
    width:22px;height:22px;border-radius:50%;
    background:var(--rose);flex:none;
    display:flex;align-items:center;justify-content:center;
  }
  .company{font-size:17px;color:var(--rose);margin-top:14px;letter-spacing:.5px}
  .address{font-size:14px;color:var(--ink);line-height:1.5;margin-top:4px}
</style>
</head>
<body>

<section class="card card--front" aria-label="Card front">
  <div class="front-brand">
    <div class="mark"><span class="brand-name">Brisk</span></div>
    <span class="front-tagline">Yoga • Swim • Pole</span>
  </div>
</section>

<section class="card card--back" aria-label="Card back">
  <div class="back-brand">
    <div class="dot"></div>
    <span class="brand-name">Brisk</span>
    <span class="tagline">Yoga • Swim • Pole</span>
  </div>

  <div class="contact">
    <p class="person-name">MARA LINWOOD</p>
    <p class="person-role">Director</p>
    <ul class="contact-list">
      <li>
        <span class="icon">
          <svg width="12" height="12" viewBox="0 0 24 24"><path fill="#fff" d="M6.6 10.8a15.1 15.1 0 0 0 6.6 6.6l2.2-2.2c.3-.3.7-.4 1-.2 1.1.4 2.3.6 3.6.6.6 0 1 .4 1 1V20c0 .6-.4 1-1 1A17 17 0 0 1 3 4c0-.6.4-1 1-1h3.5c.6 0 1 .4 1 1 0 1.2.2 2.4.6 3.6.1.3 0 .7-.2 1z"/></svg>
        </span>
        123 555 0147
      </li>
      <li>
        <span class="icon">
          <svg width="12" height="10" viewBox="0 0 24 18"><rect x="1" y="1" width="22" height="16" rx="2" fill="#fff"/><path d="M2 2l10 8 10-8" stroke="#e0407f" stroke-width="2" fill="none"/></svg>
        </span>
        mara@briskloom.com
      </li>
      <li>
        <span class="icon">
          <svg width="13" height="13" viewBox="0 0 24 24" fill="none" stroke="#fff" stroke-width="2"><circle cx="12" cy="12" r="10"/><path d="M2 12h20M12 2c3 3 3 17 0 20M12 2c-3 3-3 17 0 20"/></svg>
        </span>
        www.briskloom.com
      </li>
    </ul>
    <p class="company">BRISK LOOM PTE. LTD.</p>
    <p class="address">12 Harbour Road,<br>Singapore 628536</p>
  </div>
</section>

</body>
</html>
```